Hong Kong based International Remittance and ForEx company requires website design

We need a website designed for a new European - Hong Kong based ForEx & fund remittence entity.

The company specialises in larger corporate & high net worth private client trades, therefore the design must aesthetically reflect this (sophisticated). As a theme colour, financial entities tend to use either blue or red; if blue, our preference is a darker blue. Visually, our preference is less copy, more imagery.

Number of pages would be limited; landing (home), about us, client registration (x1 Corporate form, x1 Private Client form), Contact Us.

Have uploaded the existing logo - please note this is to be redesigned, although the colour scheme will remain the same. Please also note that copy will follow - please use Lorem Ipsum.

Target Market(s)

Medium to large Corporations. High net worth individuals.

Industry/Entity Type

Financial Service

Coding

Coded - Design and coding required

Number of Pages Required

4 page

Font styles to use
Serif

Requirements
Nice to have
• ForEx ticker,

```html
<!DOCTYPE html>
<html lang="en">
<head>
<meta charset="utf-8">
<title>Harbourline Holdings Limited</title>
<link rel="stylesheet" href="https://fonts.googleapis.com/css2?family=Alegreya:wght@500;700&family=Open+Sans:wght@400;600;700&display=swap">
<style>
:root{
  --blue:#0b4f9f;
  --blue-dark:#0a3d7c;
  --red:#e61f27;
  --ink:#333;
  --muted:#777;
  --white:#fff;
  --up:#6fd16a;
}
*{margin:0;padding:0;box-sizing:border-box}
html,body{width:1200px;height:2510px;overflow:hidden}
body{position:relative;font-family:"Open Sans",Arial,sans-serif;color:var(--ink);background:var(--white)}
.abs{position:absolute}

/* header */
.header{position:absolute;left:0;top:0;width:1200px;height:130px;background:var(--white)}
.brand{position:absolute;display:flex;align-items:center;gap:10px;font-family:"Alegreya",Georgia,serif;font-weight:500;color:var(--blue-dark)}
.brand .dot{border-radius:50%;background:var(--blue)}
.header .brand{left:87px;top:44px;font-size:40px}
.header .brand .dot{width:22px;height:22px}
.topbar{position:absolute;top:22px;font-size:13px;display:flex;align-items:center;gap:8px;color:var(--ink)}
.topbar .label{color:#aaa}
.nav{position:absolute;top:76px;left:0;width:1200px;font-size:12.5px;font-weight:600;text-transform:uppercase;color:var(--ink)}
.nav a{position:absolute;top:0;line-height:32px;text-decoration:none;color:inherit}
.nav a.active{background:var(--blue);color:var(--white);border-radius:16px;width:100px;text-align:center}

/* hero */
.hero{position:absolute;left:0;top:130px;width:1200px;height:523px;
  background:
    radial-gradient(ellipse 260px 340px at 800px 240px,rgba(20,28,45,.55),rgba(20,28,45,0) 70%),
    radial-gradient(ellipse 700px 260px at 600px 120px,rgba(200,214,232,.45),rgba(200,214,232,0) 70%),
    linear-gradient(90deg,rgba(40,70,120,.55) 0%,rgba(40,70,120,0) 30%,rgba(40,70,120,0) 70%,rgba(30,60,110,.6) 100%),
    linear-gradient(180deg,#7d93b4 0%,#5672a0 35%,#3f5b88 60%,#3a4c6a 80%,#6a7485 92%,#2e3542 100%)}
.hero-title{position:absolute;left:271px;top:196px;color:var(--white);font-family:"Alegreya",Georgia,serif;font-weight:700;font-size:41px;line-height:47px;text-shadow:0 2px 6px rgba(0,0,0,.35);white-space:nowrap}
.btn-red{position:absolute;background:var(--red);color:var(--white);font-family:"Alegreya",Georgia,serif;font-weight:700;font-size:13px;letter-spacing:1px;text-align:center;text-transform:uppercase}
.hero .btn-red{left:501px;top:312px;width:200px;height:40px;line-height:40px}

/* ticker */
.ticker{position:absolute;left:0;top:653px;width:1200px;height:117px;background:var(--blue);display:flex;align-items:center;justify-content:space-between;padding:0 18px 0 28px;color:var(--white);font-size:11px;font-weight:700}
.ticker span b{font-weight:600}
.ticker .up b{color:var(--up)}
.ticker .down b{color:var(--red)}
.ticker .up::before{content:"▲";color:var(--up);font-size:7px;margin-right:6px}
.ticker .down::before{content:"▼";color:var(--red);font-size:7px;margin-right:6px}

/* about */
.about{position:absolute;left:0;top:770px;width:1200px;height:514px}
.section-title{font-family:"Alegreya",Georgia,serif;font-weight:700;font-size:36px}
.about .section-title{position:absolute;left:82px;top:92px;color:var(--blue)}
.accent{color:var(--red)}
.lead{position:absolute;font-size:16px;line-height:25px}
.small{position:absolute;font-size:13px;line-height:24px;color:var(--muted)}
.btn-outline{position:absolute;left:85px;top:339px;width:165px;height:45px;border:2px solid var(--blue);border-radius:3px;color:var(--blue);font-family:"Alegreya",Georgia,serif;font-weight:700;font-size:13px;display:flex;align-items:center;justify-content:center;gap:16px}

/* expertise */
.expertise{position:absolute;left:0;top:1284px;width:1200px;height:514px}
.expertise .section-title{position:absolute;left:716px;top:88px;color:var(--white)}
.expertise .lead{left:708px;top:165px;width:420px;color:var(--white)}
.service{position:absolute;left:710px;display:flex;align-items:center;gap:18px;color:var(--white);font-size:16px;letter-spacing:.3px}

/* news */
.news{position:absolute;left:0;top:1798px;width:1200px;height:328px;
  background:
    radial-gradient(ellipse 260px 260px at 170px 80px,rgba(10,10,14,.75),rgba(10,10,14,0) 70%),
    radial-gradient(ellipse 800px 160px at 600px 40px,rgba(120,122,128,.5),rgba(120,122,128,0) 70%),
    linear-gradient(180deg,#55575c 0%,#3b3d42 45%,#26282c 100%)}
.news .section-title{position:absolute;left:0;width:1200px;top:82px;text-align:center;color:var(--white);font-size:34px}
.news .section-title .hl{color:#4a8fe0}
.news p{position:absolute;left:0;width:1200px;top:130px;text-align:center;color:#ddd;font-size:13.5px;line-height:22px}
.field{position:absolute;left:328px;top:204px;width:392px;height:42px;background:var(--white);display:flex;align-items:center;justify-content:space-between;padding:0 16px;font-size:12px;color:#888}
.news .btn-red{left:738px;top:204px;width:153px;height:42px;line-height:42px;font-size:12px}

/* contact */
.contact{position:absolute;left:0;top:2126px;width:1200px;height:281px}
.contact-row{position:absolute;left:0;width:470px;display:flex;align-items:center;gap:22px;padding-left:86px;color:var(--white);font-size:19px}
.contact-row.addr{font-size:16px;line-height:23px}
.divider{position:absolute;left:0;width:470px;height:1px;background:rgba(255,255,255,.35)}
.map-label{position:absolute;left:764px;top:166px;font-family:"Alegreya",Georgia,serif;font-weight:700;font-size:26px;color:#222}

/* footer */
.footer{position:absolute;left:0;top:2407px;width:1200px;height:103px;background:var(--blue)}
.footer .brand{left:87px;top:30px;font-size:32px;color:var(--white)}
.footer .brand .dot{width:18px;height:18px;background:var(--white)}
.footer-links{position:absolute;top:43px;font-family:"Alegreya",Georgia,serif;font-size:14px;color:var(--white)}
.social{position:absolute;top:46px;left:728px;display:flex;gap:20px}
.social i{display:block;width:12px;height:12px;border-radius:50%;background:var(--white)}
.copyright{position:absolute;left:954px;top:43px;font-family:"Alegreya",Georgia,serif;font-size:13px;color:var(--white)}
</style>
</head>
<body>

<header class="header">
  <div class="brand"><span class="dot"></span>Harbourline</div>
  <div class="topbar" style="left:560px"><span class="label">Language :</span><span style="margin-left:10px">ENG</span><span style="font-size:8px">▼</span></div>
  <div class="topbar" style="left:755px">
    <svg width="14" height="14" viewBox="0 0 24 24"><path fill="var(--blue)" d="M6.6 10.8a15 15 0 0 0 6.6 6.6l2.2-2.2c.3-.3.7-.4 1-.2 1.1.4 2.3.6 3.6.6.6 0 1 .4 1 1V20c0 .6-.4 1-1 1A17 17 0 0 1 3 4c0-.6.4-1 1-1h3.5c.6 0 1 .4 1 1 0 1.3.2 2.5.6 3.6.1.3 0 .7-.2 1z"/></svg>
    <span style="font-size:14px">555-014-7200</span>
  </div>
  <div class="topbar" style="left:932px">
    <svg width="15" height="12" viewBox="0 0 24 18"><rect width="24" height="18" rx="2" fill="var(--blue)"/><path d="M2 2l10 8 10-8" stroke="#fff" stroke-width="2" fill="none"/></svg>
    <span>info@harbourlinegroup.com</span>
  </div>
  <nav class="nav">
    <a class="active" style="left:402px">Home</a>
    <a style="left:532px">About Us</a>
    <a style="left:653px">Internationa Payments</a>
    <a style="left:872px">Payments Client</a>
    <a style="left:1044px">Contact Us</a>
  </nav>
</header>

<section class="hero" role="img" aria-label="Businessman standing at an office window overlooking city towers, glasses on the desk">
  <h1 class="hero-title">Harbourline Holdings Limited<br>is a regulated Money Service Operator</h1>
  <div class="btn-red">Read More</div>
</section>

<div class="ticker">
  <span class="up">ORIENT OIL <b>+0.14%</b></span>
  <span class="down">PEAKTECH GROUP <b>-0.06%</b></span>
  <span class="up">HARBOUR MOBILE <b>+0.12%</b></span>
  <span class="down">CRESTLINE INT'L <b>-0.08%</b></span>
  <span class="up">NORTHSTAR ENERGY <b>+1.11%</b></span>
  <span class="up">ORIENT OIL <b>+0.14%</b></span>
  <span class="down">PEAKTECH GROUP <b>-0.06%</b></span>
  <span class="up">HARBOUR MOBILE <b>+0.12%</b></span>
</div>

<section class="about">
  <svg class="abs" style="left:560px;top:0" width="640" height="514" role="img" aria-label="Wooden currency symbols for euro, dollar and pound on a dark surface">
    <defs>
      <linearGradient id="woodBase" x1="0" y1="0" x2="0" y2="1"><stop offset="0" stop-color="#6e5f4f"/><stop offset="1" stop-color="#4b4036"/></linearGradient>
      <radialGradient id="woodGlow" cx="0.55" cy="0.45" r="0.45"><stop offset="0" stop-color="#d9c7a6"/><stop offset="0.55" stop-color="#a88f6c" stop-opacity=".7"/><stop offset="1" stop-color="#8a7358" stop-opacity="0"/></radialGradient>
      <radialGradient id="woodShade" cx="0.2" cy="0.85" r="0.5"><stop offset="0" stop-color="#2e2620" stop-opacity=".7"/><stop offset="1" stop-color="#2e2620" stop-opacity="0"/></radialGradient>
    </defs>
    <path d="M38 0H640V514H8C-14 420 42 330 36 240 30 150 -14 70 38 0Z" fill="url(#woodBase)"/>
    <path d="M38 0H640V514H8C-14 420 42 330 36 240 30 150 -14 70 38 0Z" fill="url(#woodShade)"/>
    <path d="M38 0H640V514H8C-14 420 42 330 36 240 30 150 -14 70 38 0Z" fill="url(#woodGlow)"/>
  </svg>
  <h2 class="section-title">About <span class="accent">Harbourline</span></h2>
  <p class="lead" style="left:84px;top:165px;width:430px">Praesent congue, justo a tempus tempus, nisl lectus sollicitudin dolor non auctor elit erat .</p>
  <p class="small" style="left:84px;top:236px;width:430px">Lorem ipsum dolor sit amet, consectetur adipiscing elit. Mauris sed elementum arcu. Donec cursus ornare ipsum. Vestibulum dapibus vitae ante id finibus.</p>
  <div class="btn-outline">READ MORE <svg width="10" height="12" viewBox="0 0 10 12"><path d="M0 6h8M4 1l5 5-5 5" stroke="var(--blue)" stroke-width="2" fill="none"/></svg></div>
</section>

<section class="expertise">
  <svg class="abs" style="left:0;top:0" width="1200" height="514">
    <defs>
      <linearGradient id="suitTone" x1="0" y1="0" x2="0" y2="1"><stop offset="0" stop-color="#1f2a40"/><stop offset="0.45" stop-color="#34415a"/><stop offset="0.7" stop-color="#b9bec8"/><stop offset="1" stop-color="#eef0f2"/></linearGradient>
      <radialGradient id="shirtLight" cx="0.42" cy="0.3" r="0.35"><stop offset="0" stop-color="#dfe3ea" stop-opacity=".55"/><stop offset="1" stop-color="#dfe3ea" stop-opacity="0"/></radialGradient>
    </defs>
    <g role="img" aria-label="Businessman in a suit counting banknotes at a desk">
      <rect width="640" height="514" fill="url(#suitTone)"/>
      <rect width="640" height="514" fill="url(#shirtLight)"/>
    </g>
    <path d="M620 0H1200V514H606C580 430 592 340 588 250 584 160 600 70 620 0Z" fill="var(--blue)"/>
  </svg>
  <h2 class="section-title">Our <span class="accent">Expertise</span></h2>
  <p class="lead">Praesent congue, justo a tempus tempus, nisl lectus sollicitudin dolor non auctor elit erat .</p>
  <div class="service" style="top:260px"><svg width="38" height="38"><circle cx="19" cy="19" r="16" stroke="var(--red)" stroke-width="4" fill="none"/></svg>International Money Transfer</div>
  <div class="service" style="top:322px"><svg width="38" height="38"><circle cx="19" cy="15" r="11" fill="var(--red)"/><rect x="16" y="22" width="6" height="12" fill="var(--red)"/></svg>Foreign Exchange</div>
  <div class="service" style="top:384px"><svg width="38" height="38"><circle cx="19" cy="11" r="7" fill="var(--red)"/><path d="M7 34c0-10 5-15 12-15s12 5 12 15z" fill="var(--red)"/></svg>Paying &amp; Receiving Agency</div>
</section>

<section class="news" role="img" aria-label="Business traveller with a briefcase over a dim city skyline">
  <h2 class="section-title">Know the latest news of <span class="hl">Harbourline</span></h2>
  <p>Donec vulputate, urna ut volutpat pretium, quam diam varius nunc, sed<br>fermentum tortor urna sed nulla nulla vel magna viverra</p>
  <div class="field"><span>Enter Your Email Address</span><svg width="16" height="12" viewBox="0 0 24 18"><rect x="1" y="1" width="22" height="16" rx="2" stroke="var(--blue)" stroke-width="2" fill="none"/><path d="M2 2l10 8 10-8" stroke="var(--blue)" stroke-width="2" fill="none"/></svg></div>
  <div class="btn-red">Subscribe</div>
</section>

<section class="contact">
  <svg class="abs" style="left:0;top:0" width="1200" height="281">
    <defs>
      <radialGradient id="mapTone" cx="0.45" cy="0.5" r="0.7"><stop offset="0" stop-color="#f4f4f5"/><stop offset="1" stop-color="#dcdde0"/></radialGradient>
    </defs>
    <rect x="440" width="760" height="281" fill="url(#mapTone)" role="img" aria-label="Street map of the office neighbourhood"/>
    <path d="M0 0H455C475 60 445 120 470 175 490 225 505 260 515 281H0Z" fill="var(--red)"/>
    <path d="M823 107a18 18 0 0 0-18 18c0 14 18 32 18 32s18-18 18-32a18 18 0 0 0-18-18z" fill="var(--red)"/>
    <circle cx="823" cy="125" r="6" fill="#fff"/>
  </svg>
  <div class="contact-row" style="top:36px">
    <svg width="34" height="26" viewBox="0 0 34 26"><ellipse cx="14" cy="11" rx="12" ry="9" stroke="#fff" stroke-width="2.5" fill="none"/><path d="M24 8c5 1 8 4 8 7 0 2-1 4-3 5l1 4-5-3" stroke="#fff" stroke-width="2.5" fill="none"/></svg>
    <span style="font-weight:600">(852) 3900 4418</span>
  </div>
  <div class="divider" style="top:97px"></div>
  <div class="contact-row" style="top:122px">
    <svg width="28" height="22" viewBox="0 0 28 22"><rect x="1.5" y="1.5" width="25" height="19" stroke="#fff" stroke-width="2.5" fill="none"/><path d="M2 3l12 9 12-9" stroke="#fff" stroke-width="2.5" fill="none"/></svg>
    <span>info@harbourlineholdings.com</span>
  </div>
  <div class="divider" style="top:186px"></div>
  <div class="contact-row addr" style="top:206px">
    <svg width="26" height="30" viewBox="0 0 24 30" style="margin-left:-2px"><path d="M12 0a11 11 0 0 0-11 11c0 9 11 19 11 19s11-10 11-19A11 11 0 0 0 12 0z" fill="#fff"/><circle cx="12" cy="11" r="4" fill="var(--red)"/></svg>
    <span>48 Lantern Street Central<br>Hong Kong SAR</span>
  </div>
  <div class="map-label">Harbourline</div>
</section>

<footer class="footer">
  <div class="brand"><span class="dot"></span>Harbourline</div>
  <span class="footer-links" style="left:366px">FAQ</span>
  <span class="footer-links" style="left:427px">/</span>
  <span class="footer-links" style="left:470px">Terms</span>
  <span class="footer-links" style="left:537px">/</span>
  <span class="footer-links" style="left:581px">Privacy</span>
  <div class="social"><i></i><i></i><i></i><i></i></div>
  <span class="copyright">© 2016 All Rights Reserved.</span>
</footer>

</body>
</html>
```